Business Card Design Project

Business card based on attached logo

Todd Merrick
Todd@lorvantest.com
877-514-9073 ext. 318
Www.LorvanTest.com

Industry/Entity Type

Business

```html
<!DOCTYPE html>
<html lang="en">
<head>
<meta charset="utf-8">
<title>LorvanTest Business Cards</title>
<link rel="stylesheet" href="https://fonts.googleapis.com/css2?family=Mulish:wght@400;700;900&display=swap">
<style>
  :root {
    --stage: #ece8e3;
    --card-white: #ffffff;
    --ink: #111111;
    --text-grey: #3f3f3f;
    --brand-red: #e01f27;
    --brand-red-deep: #a31a20;
    --tint: #fce6df;
    --silver-top: #f7f7f7;
    --silver-bottom: #e1e1e1;
    --rule: #9a9a9a;
  }
  * { margin: 0; padding: 0; box-sizing: border-box; }
  html, body {
    width: 1200px;
    height: 788px;
    overflow: hidden;
  }
  body {
    position: relative;
    background: var(--stage);
    font-family: "Mulish", sans-serif;
    color: var(--ink);
  }
  .side-label {
    position: absolute;
    width: 524px;
    text-align: center;
    font-size: 20px;
    font-weight: 400;
    color: var(--ink);
  }
  .card {
    position: absolute;
    width: 524px;
    height: 298px;
    border-radius: 22px;
    overflow: hidden;
    background: var(--card-white);
  }
  .card--front  { left: 55px;  top: 75px; }
  .card--back-1 { left: 622px; top: 75px; }
  .card--back-2 { left: 55px;  top: 446px;
    background: linear-gradient(180deg, var(--brand-red) 0%, var(--brand-red-deep) 100%); }
  .card--back-3 { left: 622px; top: 446px;
    background: linear-gradient(180deg, var(--silver-top) 0%, var(--silver-bottom) 100%); }

  .brand {
    position: absolute;
    display: flex;
    align-items: flex-start;
    gap: 6px;
    font-weight: 900;
    color: var(--ink);
    letter-spacing: -1px;
    line-height: 1;
    white-space: nowrap;
  }
  .brand__mark {
    display: block;
    background: var(--brand-red);
  }
  .brand--front { left: 63px; top: 40px; font-size: 46px; }
  .brand--front .brand__mark { width: 16px; height: 16px; }
  .brand--center {
    left: 0; right: 0; top: 100px;
    justify-content: center;
    font-size: 54px;
  }
  .brand--center .brand__mark { width: 18px; height: 18px; }
  .brand--small { font-size: 40px; top: 114px; }
  .brand--small .brand__mark { width: 14px; height: 14px; }

  .tint-block {
    position: absolute;
    left: 345px; top: 100px;
    width: 150px; height: 150px;
    background: var(--tint);
  }

  .contact {
    position: absolute;
    left: 70px; top: 178px;
    width: 180px;
    height: 94px;
  }
  .contact__vrule {
    position: absolute;
    left: 12px; top: 0;
    width: 1px; height: 94px;
    background: var(--rule);
  }
  .contact__hrule {
    position: absolute;
    left: 0; top: 25px;
    width: 170px; height: 1px;
    background: var(--rule);
  }
  .contact__name {
    position: absolute;
    left: 19px; top: 5px;
    font-size: 16px;
    font-weight: 700;
    color: var(--brand-red);
  }
  .contact__list {
    position: absolute;
    left: 0; top: 29px;
    list-style: none;
  }
  .contact__item {
    display: flex;
    align-items: center;
    height: 22px;
    font-size: 13px;
    color: var(--text-grey);
  }
  .contact__icon {
    width: 10px; height: 10px;
    margin-right: 9px;
    flex: none;
  }

  .url {
    position: absolute;
    left: 0; right: 0;
    bottom: 30px;
    text-align: center;
    font-size: 17px;
    color: var(--text-grey);
  }
  .url--on-red { color: var(--card-white); }

  .plate {
    position: absolute;
    left: 81px; top: 81px;
    width: 362px; height: 128px;
    background: var(--card-white);
    border: 1px solid #d8d8d8;
  }
  .plate .brand--small { top: 42px; }
</style>
</head>
<body>

  <p class="side-label" style="left:55px; top:34px;">Front</p>
  <p class="side-label" style="left:622px; top:34px;">Back - 1</p>
  <p class="side-label" style="left:55px; top:405px;">Back - 2</p>
  <p class="side-label" style="left:622px; top:405px;">Back - 3</p>

  <section class="card card--front">
    <div class="tint-block"></div>
    <div class="brand brand--front"><span>LorvanTest</span><span class="brand__mark"></span></div>
    <div class="contact">
      <span class="contact__vrule"></span>
      <span class="contact__hrule"></span>
      <p class="contact__name">Todd Merrick</p>
      <ul class="contact__list">
        <li class="contact__item">
          <svg class="contact__icon" viewBox="0 0 10 10" aria-hidden="true"><path d="M2 1 L4 1 L4.6 3 L3.4 4 Q4.4 5.8 6 6.6 L7 5.4 L9 6 L9 8 Q5 9 2 5 Q1 3 2 1 Z" fill="var(--brand-red)"/></svg>
          877-514-9073 ext. 318
        </li>
        <li class="contact__item">
          <svg class="contact__icon" viewBox="0 0 10 10" aria-hidden="true"><rect x="0.5" y="2" width="9" height="6" fill="none" stroke="var(--brand-red)" stroke-width="1.2"/><path d="M0.5 2 L5 5.5 L9.5 2" fill="none" stroke="var(--brand-red)" stroke-width="1.2"/></svg>
          Todd@lorvantest.com
        </li>
        <li class="contact__item">
          <svg class="contact__icon" viewBox="0 0 10 10" aria-hidden="true"><circle cx="5" cy="5" r="4" fill="var(--brand-red)"/></svg>
          www.LorvanTest.com
        </li>
      </ul>
    </div>
  </section>

  <section class="card card--back-1">
    <div class="brand brand--center"><span>LorvanTest</span><span class="brand__mark"></span></div>
    <p class="url">www.LorvanTest.com</p>
  </section>

  <section class="card card--back-2">
    <div class="brand brand--center"><span>LorvanTest</span><span class="brand__mark" style="background:var(--card-white)"></span></div>
    <p class="url url--on-red">www.LorvanTest.com</p>
  </section>

  <section class="card card--back-3">
    <div class="plate">
      <div class="brand brand--center brand--small"><span>LorvanTest</span><span class="brand__mark"></span></div>
    </div>
    <p class="url">www.LorvanTest.com</p>
  </section>

</body>
</html>
```